BWP Business Card

A double sided business card based on your "Brindlewood Partners Ltd" Logo. To use the "BWP" logo on 1 side and the full company logo on the reverse.

Detials to be included:

Name: Tomas Wheeler
Postion: Consultant Orthotist & Expert Witness
T: +44 (0) 7700 938271
F: +44 (0) 7654 8820

```html
<!DOCTYPE html>
<html lang="en">
<head>
<meta charset="utf-8">
<title>BWP Business Card</title>
<link rel="stylesheet" href="https://fonts.googleapis.com/css2?family=Cinzel:wght@500;600&family=Crimson+Text:wght@400;600;700&display=swap">
<style>
  :root {
    --navy: #0d3a73;
    --grey: #9a9a9a;
    --grey-light: #b5b5b5;
    --ink-soft: #8c8c8c;
    --paper: #ffffff;
    --backdrop: #eceae6;
  }
  * { box-sizing: border-box; margin: 0; padding: 0; }
  html, body { width: 1200px; height: 720px; overflow: hidden; }
  body {
    background: var(--backdrop);
    font-family: "Crimson Text", Georgia, serif;
    position: relative;
  }
  .card {
    position: absolute;
    top: 185px;
    width: 540px;
    height: 350px;
    background: var(--paper);
    overflow: hidden;
    box-shadow: 0 2px 10px rgba(0,0,0,0.12);
  }
  .card--front { left: 40px; }
  .card--back { left: 620px; }

  .swoosh { position: absolute; inset: 0; width: 100%; height: 100%; }

  .brand {
    position: absolute;
    top: 36px;
    left: 40px;
    display: flex;
    align-items: center;
  }
  .brand__mark {
    display: flex;
    align-items: center;
    gap: 8px;
    padding-right: 16px;
    margin-right: 16px;
    border-right: 1px solid var(--grey-light);
    height: 66px;
  }
  .brand__square { width: 22px; height: 22px; background: var(--navy); }
  .brand__initials {
    font-weight: 600;
    font-size: 34px;
    color: var(--navy);
    letter-spacing: 1px;
  }
  .brand__name {
    font-family: "Cinzel", "Times New Roman", serif;
    font-weight: 600;
    font-size: 22px;
    line-height: 1.1;
    color: var(--navy);
  }
  .brand__tagline {
    margin-top: 5px;
    padding-top: 4px;
    border-top: 1px solid var(--grey-light);
    font-variant: small-caps;
    font-size: 12px;
    letter-spacing: 0.4px;
    color: var(--navy);
  }

  .contact {
    position: absolute;
    left: 44px;
    top: 148px;
  }
  .contact__name { font-weight: 700; font-size: 20px; color: var(--navy); line-height: 1.1; }
  .contact__role { font-size: 15px; color: var(--ink-soft); margin-bottom: 8px; }
  .contact__list { list-style: none; }
  .contact__item {
    display: flex;
    align-items: center;
    gap: 8px;
    font-size: 14px;
    color: var(--navy);
    line-height: 1.5;
  }
  .contact__icon { width: 12px; height: 12px; fill: var(--navy); flex: none; }

  .address {
    position: absolute;
    right: 18px;
    top: 196px;
    text-align: right;
    font-style: normal;
    font-size: 14px;
    line-height: 1.4;
    color: var(--paper);
  }

  .back-mark {
    position: absolute;
    inset: 0;
    display: flex;
    align-items: center;
    justify-content: center;
    gap: 22px;
  }
  .back-mark__square { width: 60px; height: 60px; background: var(--navy); }
  .back-mark__initials {
    font-weight: 600;
    font-size: 110px;
    color: var(--navy);
    letter-spacing: 4px;
    line-height: 1;
  }
</style>
</head>
<body>

<section class="card card--front" aria-label="Business card front">
  <svg class="swoosh" viewBox="0 0 540 350" preserveAspectRatio="none" aria-hidden="true">
    <path d="M540,44 C450,54 410,164 330,234 C250,299 110,312 0,312 L0,350 L540,350 Z" fill="var(--grey)"/>
    <path d="M540,60 C450,70 410,180 330,250 C250,315 110,328 0,328 L0,350 L540,350 Z" fill="var(--navy)"/>
    <path d="M0,350 L0,342 C110,341 210,332 300,310 C230,334 140,346 50,350 Z" fill="var(--paper)"/>
  </svg>

  <div class="brand">
    <div class="brand__mark">
      <span class="brand__square"></span>
      <span class="brand__initials">BWP</span>
    </div>
    <div class="brand__text">
      <div class="brand__name">Brindlewood<br>Partners Ltd</div>
      <div class="brand__tagline">Excellence in Medical Legal Reporting</div>
    </div>
  </div>

  <div class="contact">
    <div class="contact__name">Tomas Wheeler</div>
    <div class="contact__role">Consultant Orthotist &amp; Expert Witness</div>
    <ul class="contact__list">
      <li class="contact__item">
        <svg class="contact__icon" viewBox="0 0 24 24"><path d="M6.6 10.8a15 15 0 0 0 6.6 6.6l2.2-2.2a1 1 0 0 1 1-.25 11.4 11.4 0 0 0 3.6.57 1 1 0 0 1 1 1V20a1 1 0 0 1-1 1A17 17 0 0 1 3 4a1 1 0 0 1 1-1h3.5a1 1 0 0 1 1 1c0 1.25.2 2.45.57 3.57a1 1 0 0 1-.25 1z"/></svg>
        +44 (0) 7700 938271
      </li>
      <li class="contact__item">
        <svg class="contact__icon" viewBox="0 0 24 24"><path d="M6 3h10v5H6z M3 9h18v9h-3v3H6v-3H3z M8 15v4h8v-4z"/></svg>
        +44 (0) 7654 8820
      </li>
      <li class="contact__item">
        <svg class="contact__icon" viewBox="0 0 24 24"><path d="M2 5h20v14H2z M4 7v.5l8 5 8-5V7l-8 5z" fill-rule="evenodd"/></svg>
        tomas@brindlewoodpartners.co.uk
      </li>
    </ul>
  </div>

  <address class="address">
    18 Larkfield Kingsbury<br>
    Surrey, KT4 2RN
  </address>
</section>

<section class="card card--back" aria-label="Business card back">
  <div class="back-mark">
    <span class="back-mark__square"></span>
    <span class="back-mark__initials">BWP</span>
  </div>
</section>

</body>
</html>
```